Church needs a street sign design

We're a small church located in Silicon Valley, California. Our website is https://www.vgtmarlowfield.org/ and our address is 4817 Ferrow Ave, San Jose, California, 95873. You can look up our location on Google Maps to see the sign from Street View. I have uploaded an image of the street sign as well. The marquee, the top section of the sign, and the separating line between them both will be removed. We're seeking a design for a new backlit acrylic insert that will go on the front of the light box and the back of the lightbox. The acrylic sign will fill the entire external frame. In the future, we may build a decorative wood frame around the structural legs, as visualized in one of the uploaded files. The church's brand colors are: #003366 (dark blue), #ff6600 (vibrant orange), #228b22 (forest green). I have also uploaded the church's logo assets. Our primary font is Montserrat and the secondary is Poppins. You can deviate from these colors/fonts if the sign is still coherent with the rest of our branding. Our branding values are mission, truth, passion, and community (please do not put those words on the sign! They are just intended to guide the look of the design). The sign dimensions are 96" by 47.5". Keep in mind that the sign will be backlit on a busy street side. It will also be positioned next to an old-looking church building. We do NOT want a sign that looks traditional, old, or antiquated. Instead, we want a modern-looking sign that pairs well with our old building while helping it look more modern too. We would also like the web address clearly visible on the sign: vgtmarlowfield.org. If you have any questions, just let me know!

```html
<!DOCTYPE html>
<html lang="en">
<head>
<meta charset="utf-8">
<title>Marlow Community Church – Street Sign</title>
<link rel="stylesheet" href="https://fonts.googleapis.com/css2?family=Montserrat:wght@600&family=Poppins:wght@600;700&display=swap">
<style>
  :root {
    --backdrop: #b3bac7;
    --sign-white: #ffffff;
    --ink: #111111;
    --orange: #ff7a00;
    --orange-deep: #ff4d00;
    --red: #ff1a00;
    --navy: #0b2f5e;
    --pin-dot: #ff7a00;
    --text-light: #ffffff;
  }
  * { margin: 0; padding: 0; box-sizing: border-box; }
  html, body {
    width: 762px; height: 1200px; overflow: hidden;
    background: var(--backdrop);
  }
  .canvas { position: relative; width: 762px; height: 1200px; }

  .sign {
    position: absolute; left: 64px; top: 442px;
    width: 636px; height: 315px;
    background: var(--sign-white);
    box-shadow: 0 10px 14px rgba(0,0,0,0.35);
    overflow: hidden;
  }

  .brand-square {
    position: absolute; left: 66px; top: 40px;
    width: 100px; height: 100px;
    background: var(--ink);
  }
  .brand-name {
    position: absolute; left: 204px; top: 34px;
    font-family: "Montserrat", sans-serif; font-weight: 600;
    color: var(--ink); white-space: nowrap; line-height: 1;
  }
  .brand-name__main { display: block; font-size: 76px; letter-spacing: -1px; }
  .brand-name__sub { display: block; font-size: 33px; margin-top: 2px; letter-spacing: 0.2px; }

  .info-band {
    position: absolute; left: 31px; top: 155px;
    width: 605px; height: 135px;
    border-radius: 20px 0 0 20px;
    background: linear-gradient(100deg, var(--orange) 0%, var(--orange-deep) 55%, var(--red) 100%);
  }

  .pin { position: absolute; left: 163px; top: 180px; width: 28px; height: 40px; }

  .location, .address, .website {
    position: absolute; font-family: "Poppins", sans-serif;
    color: var(--text-light); white-space: nowrap; line-height: 1;
  }
  .location { left: 197px; top: 177px; font-size: 27.5px; font-weight: 700; }
  .address  { left: 199px; top: 208px; font-size: 17.5px; font-weight: 600; }
  .website  { left: 162px; top: 234px; font-size: 36px; font-weight: 700; letter-spacing: -0.5px; }
</style>
</head>
<body>
<main class="canvas">
  <section class="sign">
    <div class="brand-square"></div>
    <h1 class="brand-name">
      <span class="brand-name__main">MARLOW</span>
      <span class="brand-name__sub">COMMUNITY CHURCH</span>
    </h1>

    <div class="info-band" role="img" aria-label="Orange and red sky with soft clouds"></div>

    <svg class="pin" viewBox="0 0 28 40" aria-hidden="true">
      <path d="M14 0C6.3 0 0 6.2 0 13.8 0 23.5 14 40 14 40s14-16.5 14-26.2C28 6.2 21.7 0 14 0z" fill="var(--navy)"/>
      <circle cx="14" cy="13.5" r="6" fill="var(--pin-dot)"/>
    </svg>
    <p class="location">SILICON VALLEY, CALIFORNIA</p>
    <p class="address">4817 Ferrow Ave, San Jose, California, 95873</p>
    <p class="website">www.vgtmarlowfield.org</p>
  </section>
</main>
</body>
</html>
```